Regional Job Board needs a powerpoint design

Looking for a powerful design for a new company in Cheshire, UK.
Our product is a job board that is targeted at local job seekers and employers within a certain region's of the UK.
The theme is Local people for Local Jobs, the Website is feature rich with job board technology, so looking to use the powerpoint to communicate screen shots and features across the presentation, including a strong education and community theme to support the feel. Modern, professional, colourful,

Industry/Entity Type

It Company

```html
<!DOCTYPE html>
<html lang="en">
<head>
<meta charset="utf-8">
<title>Project Title Here</title>
<link rel="stylesheet" href="https://fonts.googleapis.com/css2?family=Oswald:wght@600&family=Roboto+Condensed:wght@400;700&display=swap">
<style>
  :root {
    --brand-blue: #21a0db;
    --brand-orange: #f58220;
    --rule-tan: #e8b27a;
    --page-bg: #f1f1f1;
    --body-grey: #6a6a6a;
    --white: #ffffff;
  }
  * { margin: 0; padding: 0; box-sizing: border-box; }
  html, body { width: 1200px; height: 900px; overflow: hidden; }
  body { background: var(--page-bg); font-family: "Roboto Condensed", Arial, sans-serif; }

  .slide {
    position: relative;
    width: 1200px;
    height: 900px;
    overflow: hidden;
    background: radial-gradient(circle at 20% 55%, #ebebeb 0, var(--page-bg) 60%);
  }

  .header-bar {
    position: absolute;
    top: 0; left: 0;
    width: 1200px;
    height: 99px;
    background: var(--brand-blue);
    border-bottom: 3px solid var(--rule-tan);
  }
  .slide-title {
    position: absolute;
    left: 28px;
    top: 12px;
    font-family: "Oswald", "Arial Narrow", sans-serif;
    font-weight: 600;
    font-size: 52px;
    line-height: 72px;
    color: var(--white);
  }
  .brand {
    position: absolute;
    right: 14px;
    top: 30px;
    display: flex;
    align-items: center;
    gap: 10px;
  }
  .brand-dot {
    width: 34px; height: 34px;
    border-radius: 50%;
    background: var(--white);
  }
  .brand-name {
    font-family: "Roboto Condensed", Arial, sans-serif;
    font-weight: 700;
    font-size: 27px;
    color: var(--white);
  }

  .content-column {
    position: absolute;
    top: 172px;
    width: 420px;
  }
  .content-column.left { left: 70px; }
  .content-column.right { left: 657px; }

  .column-heading {
    font-family: "Roboto Condensed", Arial, sans-serif;
    font-weight: 700;
    font-size: 25px;
    line-height: 40px;
    color: var(--brand-orange);
    margin-bottom: 6px;
  }
  .column-body {
    font-size: 20.5px;
    line-height: 36px;
    color: var(--body-grey);
  }

  .footer-bar {
    position: absolute;
    left: 0; bottom: 0;
    width: 1200px;
    height: 36px;
    background: var(--brand-orange);
  }
</style>
</head>
<body>
  <main class="slide">
    <header class="header-bar">
      <h1 class="slide-title">Project Title Here</h1>
      <div class="brand">
        <span class="brand-dot"></span>
        <span class="brand-name">HometownWorkNet</span>
      </div>
    </header>

    <section class="content-column left">
      <h2 class="column-heading">Subtext here Subtext here</h2>
      <p class="column-body">Subtext here Subtext here Subtext here Subtext here Subtext here Subtext here Subtext here Subtext here Subtext here Subtext here Subtext here Subtext here Subtext here Subtext here Subtext here Subtext here Subtext here Subtext here Subtext here Subtext here Subtext here Subtext here Subtext here Subtext here Subtext here Subtext here Subtext here Subtext here Subtext here Subtext here Subtext here Subtext here Subtext here Subtext here Subtext here Subtext here Subtext here Subtext here Subtext here Subtext here Subtext here Subtext here Subtext here Subtext here Subtext here Subtext here Subtext here Subtext here Subtext here Subtext here Subtext here Subtext here Subtext here Subtext here Subtext here Subtext here Subtext here Subtext here</p>
    </section>

    <section class="content-column right">
      <h2 class="column-heading">Subtext here Subtext here</h2>
      <p class="column-body">Subtext here Subtext here Subtext here Subtext here Subtext here Subtext here Subtext here Subtext here Subtext here Subtext here Subtext here Subtext here Subtext here Subtext here Subtext here Subtext here Subtext here Subtext here Subtext here Subtext here Subtext here Subtext here Subtext here Subtext here Subtext here Subtext here Subtext here Subtext here Subtext here Subtext here Subtext here Subtext here Subtext here Subtext here Subtext here Subtext here Subtext here Subtext here Subtext here Subtext here Subtext here Subtext here Subtext here Subtext here Subtext here Subtext here Subtext here Subtext here Subtext here Subtext here Subtext here Subtext here Subtext here Subtext here Subtext here Subtext here Subtext here Subtext here</p>
    </section>

    <footer class="footer-bar"></footer>
  </main>
</body>
</html>
```